African homeware retailer needs a web page design

We need a web page design for a new homeware and accessories store based in Johannesburg, South Africa. Our store carries modern African inspired items from designers that support social development and poverty alleviation initiatives. We have a particular preference for outfits that are centred on the empowerment of women.

Our business celebrates the skill, design and product of African craft and the work of designers looking to take that forward in a socially beneficial way (creating employment, developing skills, supporting local crafts people etc). We aim to carry items and inspirations from all over the African continent.

We would like to see a design that communicates African beauty and elegance without the typical tribal references that are made in reference to African craft or art.

We would like the web page to be stylish, uncomplicated, modern, captivating and appealing to the discerning customer. A similar value proposition is that of http://www.marlowtenwick.example/.

This is an e-commerce website which must be attractive to both individual buyers and design professionals so the website needs to look professional.

Here are links to some websites we like:
http://www.quenbyhollis.example/
http://www.dravelo.example/

Our logo is attached to the brief.

Target Market(s)

Our target market is female, age 20-50. However should not alienate the design conscious male customer therefore

Industry/Entity Type

E-Commerce

Requirements
Must have
• - A featured product banner which includes a photograph and text. This should be easy to edit as we will be changing the featured product regularly
- An easily expendable products section with categories. Examples of categories could be cushions, bedding, crockery etc. Should be easy to add new categories as well as new product pictures
- Home/landing page should be uncluttered
- Should use the logo and should be easy to change the logo which we have in various colour combinations. We plan to change the logo colours depending on circumstance e.g. make it red and white around Valentines day (similar to the way Vintrel frequently changes the logo on their landing page)

```html
<!DOCTYPE html>
<html lang="en">
<head>
<meta charset="utf-8">
<title>Kaya Veld — Homeware &amp; Accessories</title>
<link rel="stylesheet" href="https://fonts.googleapis.com/css2?family=Ubuntu:wght@400;500;700&family=Oxygen:wght@400;700&family=Kaushan+Script&display=swap">
<style>
:root{
  --page-bg:#eef0f1;
  --sheet:#fbfbfb;
  --rule:#d9dcdc;
  --teal:#1f7a78;
  --mint:#6dbb9f;
  --mint-soft:#cfe9df;
  --orange:#e8471c;
  --coral:#e55a50;
  --amber:#f9b13b;
  --plum:#5a4048;
  --ink:#333;
  --muted:#666;
}
*{box-sizing:border-box;margin:0;padding:0}
html,body{width:1013px;height:1200px;overflow:hidden}
body{background:var(--page-bg);font-family:"Oxygen",sans-serif;color:var(--ink)}
.page{position:relative;width:1013px;height:1200px;overflow:hidden}
.sheet{position:absolute;left:110px;top:0;width:792px;height:1200px;background:var(--sheet);border-left:1px solid #e2e4e4;border-right:1px solid #e2e4e4}
.abs{position:absolute}

/* header */
.brand{left:136px;top:26px;display:flex;align-items:center;gap:18px}
.brand-mark{width:70px;height:70px;background:var(--orange);transform:rotate(45deg);margin:14px}
.brand-name{font-family:"Ubuntu",sans-serif;font-weight:500;color:var(--orange);font-size:30px;letter-spacing:2px;line-height:1;white-space:nowrap}
.brand-tag{font-family:"Oxygen",sans-serif;font-size:8px;color:var(--teal);margin-top:6px;letter-spacing:.5px;text-align:center;white-space:nowrap}
.search{left:435px;top:74px;width:215px;height:25px;display:flex;border:1px solid var(--rule);background:#fff}
.search span{flex:1;font-size:10px;color:#888;padding:6px 9px;font-family:"Ubuntu",sans-serif}
.search b{width:28px;background:var(--amber);display:flex;align-items:center;justify-content:center}
.social-top{left:656px;top:81px;width:104px;display:flex;justify-content:space-between;font-family:"Ubuntu",sans-serif;font-size:8px;color:var(--mint);white-space:nowrap}
.agent{left:766px;top:75px;width:110px;height:23px;background:var(--mint-soft);font-family:"Ubuntu",sans-serif;font-size:11px;color:#3a3a3a;display:flex;align-items:center;justify-content:center}

/* navigation */
.nav{top:140px;font-family:"Ubuntu",sans-serif;font-weight:700;font-size:11.5px;letter-spacing:.3px}
.nav-link{color:var(--orange)}
.nav-home{color:var(--teal)}
.nav-sep{top:141px;width:1px;height:11px;background:var(--rule)}
.nav-btn{top:131px;height:29px;color:#fff;font-family:"Ubuntu",sans-serif;font-weight:700;font-size:11.5px;display:flex;align-items:center;justify-content:center}
.blog{left:816px;top:128px;width:61px;height:34px;background:var(--mint);border-radius:20px 20px 20px 4px;color:#fff;font-family:"Ubuntu",sans-serif;font-size:17px;display:flex;align-items:center;justify-content:center}

/* banner */
.hero{left:136px;top:176px;width:741px;height:324px;background:linear-gradient(160deg,#d9d9d6 0%,#cfcdc7 35%,#b9c15a 48%,#cfcdc7 60%,#c73a46 78%,#d3cfca 100%)}
.hero-text{left:153px;top:203px;width:340px;font-family:"Kaushan Script",cursive;color:#fff;font-size:18px;line-height:27px}
.dots{left:465px;top:512px;display:flex;gap:12px}
.dots i{display:block;width:11px;height:11px;background:var(--orange);transform:rotate(45deg)}
.dots i.on{background:var(--teal)}

/* categories */
.cat{top:544px;width:200px;text-align:center}
.cat h2{font-family:"Ubuntu",sans-serif;font-weight:700;font-size:22px;letter-spacing:.5px;line-height:26px}
.cat-img{width:88px;height:88px;transform:rotate(45deg);margin:24px auto 0}
.cat p{font-size:10px;color:var(--muted);line-height:13px;margin-top:25px}
.buy{display:block;width:140px;height:30px;margin:6px auto 0;background:var(--mint);color:#fff;font-family:"Ubuntu",sans-serif;font-weight:700;font-size:14px;line-height:30px}

/* lower panels */
.panel-title{top:796px;width:235px;font-family:"Ubuntu",sans-serif;font-size:11.5px;color:#333;letter-spacing:.2px}
.panel-rule{top:815px;width:235px;height:1px;background:var(--rule)}
.panel-rule::before{content:"";position:absolute;left:0;top:-1px;width:64px;height:3px;background:var(--teal)}
.catalog{left:152px;top:844px;width:180px;height:116px;background:linear-gradient(120deg,#b94a3c,#8c8f7a 45%,#4e4a62 70%,#b48a52)}
.news-mark{left:396px;top:851px;width:28px;height:28px;background:var(--orange);transform:rotate(45deg)}
.news-text{left:438px;top:853px;width:180px;font-size:10px;color:var(--muted);line-height:13px}
.email{left:390px;top:901px;width:234px;height:25px;border:1px solid var(--rule);background:#fff;display:flex}
.email span{flex:1;font-family:"Ubuntu",sans-serif;font-size:10px;color:#777;padding:6px 8px}
.email b{width:29px;background:var(--amber);display:flex;align-items:center;justify-content:center}
.artisan{left:642px;width:235px;display:flex;gap:17px}
.artisan-photo{width:44px;height:46px;flex:none;background:linear-gradient(180deg,#5b5650,#8c7b6a 60%,#3d3834)}
.artisan h3{font-family:"Oxygen",sans-serif;font-weight:700;font-size:10.5px;color:#333;line-height:13px}
.artisan p{font-size:10.5px;color:#444;line-height:13px;margin-top:5px}
.artisan-rule{left:642px;top:966px;width:227px;height:1px;background:var(--rule)}

/* footer */
.foot-line{left:136px;width:741px;height:1px;background:var(--rule)}
.foot-h{top:1009px;font-family:"Ubuntu",sans-serif;font-weight:700;font-size:12.5px;color:#333}
.quick-links a{position:absolute;font-family:"Ubuntu",sans-serif;font-size:10.5px;color:#333;text-decoration:none}
.field{left:344px;width:134px;height:19px;border:1px solid #bbb;border-radius:2px;background:#fff;font-size:10px;font-style:italic;color:#777;padding:2px 7px;font-family:"Ubuntu",sans-serif}
.submit{left:344px;top:1127px;width:54px;height:18px;background:#d9381e;color:#fff;font-family:"Ubuntu",sans-serif;font-weight:700;font-size:11px;display:flex;align-items:center;justify-content:center;border-radius:2px}
.pay{height:16px;background:#fff;border:1px solid #e2e2e2;font-family:"Ubuntu",sans-serif;font-size:7px;color:#23408e;display:flex;align-items:center;justify-content:center}
.pay-lg{height:20px;font-size:11px;font-weight:700;border:none;background:none}
.social-foot{left:558px;top:1128px;display:flex;gap:8px;font-family:"Ubuntu",sans-serif;font-size:9px;color:var(--mint)}
.foot-brand{left:770px;top:1030px;width:120px;text-align:center}
.foot-brand .brand-mark{width:44px;height:44px;margin:10px auto 18px}
.foot-brand .brand-name{font-size:15px;letter-spacing:1px}
.foot-brand .brand-tag{font-size:6px;margin-top:3px}
.copyright{left:136px;top:1173px;width:741px;text-align:center;font-family:"Ubuntu",sans-serif;font-size:10px;color:#555}
</style>
</head>
<body>
<div class="page">
  <div class="sheet"></div>

  <!-- header -->
  <div class="abs brand">
    <div class="brand-mark"></div>
    <div>
      <div class="brand-name">KAYA VELD</div>
      <div class="brand-tag">homeware &amp; accessories</div>
    </div>
  </div>
  <div class="abs search"><span>SEARCH OUR SITE</span><b>
    <svg width="11" height="11" viewBox="0 0 12 12"><circle cx="5" cy="5" r="3.5" fill="none" stroke="#fff" stroke-width="1.5"/><line x1="7.6" y1="7.6" x2="11" y2="11" stroke="#fff" stroke-width="1.6"/></svg>
  </b></div>
  <div class="abs social-top"><span>Gathera</span><span>Chirply</span><span>Tackboard</span></div>
  <div class="abs agent">AGENT SIGN-IN</div>

  <!-- navigation -->
  <a class="abs nav nav-home" style="left:137px">HOME</a>
  <span class="abs nav-sep" style="left:198px"></span>
  <a class="abs nav nav-link" style="left:223px">ABOUT US</a>
  <span class="abs nav-sep" style="left:309px"></span>
  <a class="abs nav nav-link" style="left:334px">PRODUCTS</a>
  <span class="abs nav-sep" style="left:424px"></span>
  <a class="abs nav nav-link" style="left:450px">CONTACT US</a>
  <a class="abs nav-btn" style="left:543px;width:89px;background:var(--plum)">SHOP NOW</a>
  <a class="abs nav-btn" style="left:635px;width:101px;background:var(--coral)">LOREM IPSAM</a>
  <a class="abs nav-btn" style="left:740px;width:69px;background:var(--amber)">JOIN US</a>
  <a class="abs blog">blog</a>

  <!-- featured banner -->
  <div class="abs hero" role="img" aria-label="Featured product photo: beaded wire lizard ornaments in green and red"></div>
  <div class="abs hero-text">Lorem ipsum dolor sit amet, consectet adipiscing elit, sed diam nonummy</div>
  <div class="abs dots"><i></i><i class="on"></i><i></i><i></i></div>

  <!-- categories -->
  <div class="abs cat" style="left:153px">
    <h2 style="color:var(--plum)">CUSHIONS</h2>
    <div class="cat-img" role="img" aria-label="Patterned cushions product photo" style="background:linear-gradient(135deg,#f3d6c8,#c0392b 45%,#3c4fa0 60%,#f3d6c8)"></div>
    <p>Lorem ipsum dolor sit amet, consectet<br>adipiscing elit, sed diam nonum</p>
    <a class="buy">BUY NOW</a>
  </div>
  <div class="abs cat" style="left:406px">
    <h2 style="color:var(--coral)">BEDDING</h2>
    <div class="cat-img" role="img" aria-label="White bed linen product photo" style="background:linear-gradient(135deg,#f3d6c8,#eeeeee 40%,#dcdcdc 60%,#f3d6c8)"></div>
    <p>Lorem ipsum dolor sit amet, consectet<br>adipiscing elit, sed diam nonum</p>
    <a class="buy">BUY NOW</a>
  </div>
  <div class="abs cat" style="left:659px">
    <h2 style="color:var(--amber)">CROCKERY</h2>
    <div class="cat-img" role="img" aria-label="Woven plates product photo" style="background:linear-gradient(135deg,#f3d6c8,#b8392e 45%,#5a2a2a 60%,#f3d6c8)"></div>
    <p>Lorem ipsum dolor sit amet, consectet<br>adipiscing elit, sed diam nonum</p>
    <a class="buy">BUY NOW</a>
  </div>

  <!-- catalog / newsletter / artisans -->
  <div class="abs panel-title" style="left:136px">VIEW OUR CATALOG</div>
  <div class="abs panel-rule" style="left:136px"></div>
  <div class="abs panel-title" style="left:389px">DON'T MISS OUT AGAIN</div>
  <div class="abs panel-rule" style="left:389px"></div>
  <div class="abs panel-title" style="left:642px">MEET OUR ARTISTIAN</div>
  <div class="abs panel-rule" style="left:642px"></div>

  <div class="abs catalog" role="img" aria-label="Two craft magazine catalogue covers"></div>

  <div class="abs news-mark"></div>
  <div class="abs news-text">Lorem ipsum dolor sit amet, consectet adipiscing elit, sed diam nonummy</div>
  <div class="abs email"><span>ENTER EMAIL ADDRESS</span><b>
    <svg width="13" height="9" viewBox="0 0 13 9"><rect x=".5" y=".5" width="12" height="8" fill="none" stroke="#fff"/><polyline points=".5,.5 6.5,5 12.5,.5" fill="none" stroke="#fff"/></svg>
  </b></div>

  <div class="abs artisan" style="top:844px">
    <div class="artisan-photo" role="img" aria-label="Portrait photo of an artisan"></div>
    <div><h3>Lorem ipsum dolor sitamet conse</h3><p>Lorem ipsum dolor sit amet,<br>consectet adipisc eli sed</p></div>
  </div>
  <div class="abs artisan" style="top:907px">
    <div class="artisan-photo" role="img" aria-label="Portrait photo of an artisan"></div>
    <div><h3>Lorem ipsum dolor sitamet conse</h3><p>Lorem ipsum dolor sit amet,<br>consectet adipisc eli sed</p></div>
  </div>
  <div class="abs artisan-rule"></div>

  <!-- footer -->
  <div class="abs foot-line" style="top:992px"></div>

  <div class="abs foot-h" style="left:137px">Quick Links</div>
  <nav class="quick-links">
    <a style="left:137px;top:1033px">HOME</a>
    <a style="left:137px;top:1057px">ABOUT US</a>
    <a style="left:137px;top:1082px">PRODUCTS</a>
    <a style="left:137px;top:1106px">CONTACT US</a>
    <a style="left:137px;top:1131px">SHOP NOW</a>
    <a style="left:221px;top:1033px">JOIN US</a>
    <a style="left:221px;top:1057px">BLOG</a>
    <a style="left:221px;top:1082px">SITE MAP</a>
  </nav>

  <div class="abs foot-h" style="left:345px">Quick Contact</div>
  <div class="abs field" style="top:1034px">Name</div>
  <div class="abs field" style="top:1060px">Email</div>
  <div class="abs field" style="top:1086px;height:34px">Message</div>
  <div class="abs submit">Submit</div>

  <div class="abs foot-h" style="left:559px">We Accept</div>
  <div class="abs pay" style="left:558px;top:1034px;width:25px">Norvia</div>
  <div class="abs pay" style="left:594px;top:1034px;width:27px">Orbcard</div>
  <div class="abs pay" style="left:630px;top:1034px;width:26px">Centrix</div>
  <div class="abs pay" style="left:665px;top:1034px;width:26px">Findra</div>
  <div class="abs pay pay-lg" style="left:558px;top:1065px;width:60px">Paywell</div>
  <div class="abs pay pay-lg" style="left:630px;top:1065px;width:54px;color:#222">Banklink</div>

  <div class="abs foot-h" style="left:558px;top:1101px">Connect With Us</div>
  <div class="abs social-foot"><span>Gathera</span><span>Chirply</span><span>Tackboard</span></div>

  <div class="abs foot-brand">
    <div class="brand-mark"></div>
    <div class="brand-name">KAYA VELD</div>
    <div class="brand-tag">homeware &amp; accessories</div>
  </div>

  <div class="abs foot-line" style="top:1162px"></div>
  <div class="abs copyright">© 2014 Kayaveld. All Rights Reserved.</div>
</div>
</body>
</html>
```